Standardization and redesign of graphics for a non-fiction book

For a book project, 11 graphics need to be visually unified so that all the graphics in the book are in the same style. The graphics must be created from scratch. Just new colors aren't enough. Some of the existing graphics are by other authors who own the copyright. Accordingly, the new graphics must be truly new. This is especially true for the "2 S-curves" graphic.

Target Market(s)

Manager Furniture Industry

Industry/Entity Type

Möbel

Colors
0054AA
0677BA
7BADD7
CADEEF
E8F1F8

```html
<!DOCTYPE html>
<html lang="de">
<head>
<meta charset="utf-8">
<title>Geschäftsmodell-Dreieck</title>
<link rel="preconnect" href="https://fonts.googleapis.com">
<link href="https://fonts.googleapis.com/css2?family=Poppins:wght@600;700&display=swap" rel="stylesheet">
<style>
  :root {
    --brand-deep: #0054aa;
    --brand-mid: #0677ba;
    --brand-soft: #7badd7;
    --brand-pale: #cadeef;
    --brand-mist: #e8f1f8;
    --ink: #3a4460;
    --edge: #cadeef;
    --divider: #b9d1e8;
    --paper: #ffffff;
  }
  html, body {
    margin: 0;
    padding: 0;
    width: 1199px;
    height: 1200px;
    overflow: hidden;
    background: var(--paper);
  }
  .diagram {
    display: block;
    width: 1199px;
    height: 1200px;
    font-family: "Poppins", sans-serif;
  }
  .triangle-panel { stroke: var(--edge); stroke-width: 6; stroke-linejoin: round; }
  .divider { stroke: var(--divider); stroke-width: 6; }
  .node { fill: var(--brand-soft); }
  .node-core { fill: var(--brand-deep); }
  .question {
    fill: var(--ink);
    font-size: 25px;
    font-weight: 600;
    text-anchor: middle;
  }
  .segment-label {
    fill: var(--ink);
    font-size: 33px;
    font-weight: 700;
    text-anchor: middle;
  }
  .node-label {
    fill: var(--ink);
    font-size: 36px;
    font-weight: 700;
    text-anchor: middle;
    dominant-baseline: central;
  }
  .node-label--core { fill: #ffffff; }
</style>
</head>
<body>
<svg class="diagram" viewBox="0 0 1500 1500" xmlns="http://www.w3.org/2000/svg" role="img" aria-label="Magisches Dreieck des Geschäftsmodells: Wer, Was, Wie, Wert">
  <defs>
    <linearGradient id="panel-fill" x1="0" y1="0" x2="1" y2="0.3">
      <stop offset="0" stop-color="#ffffff"/>
      <stop offset="1" stop-color="#e8f1f8"/>
    </linearGradient>
  </defs>

  <g class="triangle">
    <polygon class="triangle-panel" fill="url(#panel-fill)" points="736,458 1120,1073 352,1073"/>
    <line class="divider" x1="736" y1="847" x2="553" y2="762"/>
    <line class="divider" x1="736" y1="847" x2="920" y2="765"/>
    <line class="divider" x1="736" y1="847" x2="736" y2="1073"/>
  </g>

  <g class="segment-labels">
    <text class="segment-label"><tspan x="733" y="688">Nutzenver-</tspan><tspan x="733" y="723">sprechen</tspan></text>
    <text class="segment-label"><tspan x="583" y="973">Ertrags-</tspan><tspan x="583" y="1008">mechanik</tspan></text>
    <text class="segment-label"><tspan x="890" y="955">Wert-</tspan><tspan x="890" y="990">schöpfungs-</tspan><tspan x="890" y="1025">kette</tspan></text>
  </g>

  <g class="nodes">
    <circle class="node" cx="736" cy="522" r="101"/>
    <text class="node-label" x="736" y="522">Was?</text>

    <circle class="node" cx="362" cy="1073" r="101"/>
    <text class="node-label" x="362" y="1073">Wert?</text>

    <circle class="node" cx="1112" cy="1073" r="101"/>
    <text class="node-label" x="1112" y="1073">Wie?</text>

    <circle class="node-core" cx="736" cy="847" r="101"/>
    <text class="node-label node-label--core" x="736" y="847">Wer?</text>
  </g>

  <g class="questions">
    <text class="question"><tspan x="736" y="346">Was bieten wir dem</tspan><tspan x="736" y="384">Kunden an?</tspan></text>
    <text class="question"><tspan x="298" y="913">Wie wird Wert</tspan><tspan x="298" y="950">erzielt?</tspan></text>
    <text class="question"><tspan x="1173" y="913">Wie stellen wir die</tspan><tspan x="1173" y="950">Leistung her?</tspan></text>
    <text class="question"><tspan x="737" y="1130">Wer sind unsere</tspan><tspan x="737" y="1168">Zielkunden?</tspan></text>
  </g>
</svg>
</body>
</html>
```